New bussiness card, using company logo.
Lionel Brisk
Manager/Director
Brisk Property Developments
Po Box 5347
Thuringowa Central
Qld
0491 638 205
lionel@briskpropertydevelopments
eye catching, vibrant colours, professional

```html
<!DOCTYPE html>
<html lang="en">
<head>
<meta charset="utf-8">
<title>Brisk Property Developments – Business Cards</title>
<link rel="stylesheet" href="https://fonts.googleapis.com/css2?family=Open+Sans:wght@400;600;700&display=swap">
<style>
  :root {
    --backdrop: #2a2624;
    --red: #e0242b;
    --green: #6cbd45;
    --green-light: #8dc63f;
    --white: #ffffff;
    --ink: #2b2b2b;
    --grey: #555555;
  }
  * { box-sizing: border-box; margin: 0; padding: 0; }
  html, body { width: 1200px; height: 736px; overflow: hidden; }
  body {
    position: relative;
    background: var(--backdrop);
    font-family: "Open Sans", Arial, sans-serif;
  }
  .card {
    position: absolute;
    width: 556px;
    height: 316px;
    border-radius: 22px;
    overflow: hidden;
  }
  .card--front { left: 27px; top: 36px; background: var(--white); }
  .card--red { left: 609px; top: 36px; background: var(--red); }
  .card--white { left: 27px; top: 385px; background: var(--white); }
  .card--green { left: 612px; top: 385px; background: linear-gradient(90deg, var(--green-light), var(--green)); }

  .swoosh { position: absolute; inset: 0; }

  .company-name {
    position: absolute;
    font-weight: 700;
    white-space: nowrap;
  }
  .card--front .company-name { left: 41px; top: 74px; font-size: 20px; color: var(--red); }
  .card--red .company-name,
  .card--white .company-name,
  .card--green .company-name { left: 0; right: 0; text-align: center; font-size: 30px; }
  .card--red .company-name { top: 140px; color: var(--white); }
  .card--white .company-name { top: 128px; color: var(--red); }
  .card--green .company-name { top: 140px; color: var(--white); }

  .holder { position: absolute; left: 41px; top: 200px; }
  .holder__name { font-size: 17px; font-weight: 700; color: var(--red); line-height: 22px; }
  .holder__role { font-size: 13px; color: var(--grey); line-height: 18px; }

  .address {
    position: absolute; right: 22px; top: 198px;
    text-align: right; font-size: 14px; line-height: 20px; color: var(--white);
  }
  .contact {
    position: absolute; right: 22px; top: 262px;
    text-align: right; font-size: 14px; line-height: 22px; color: var(--white);
  }
  .contact__line { display: flex; justify-content: flex-end; align-items: center; gap: 6px; }
  .contact__icon { width: 11px; height: 11px; }

  .website {
    position: absolute; left: 0; right: 0; top: 275px;
    text-align: center; font-size: 15px; letter-spacing: 1px;
  }
  .card--red .website, .card--green .website { color: var(--white); }
  .card--white .website { color: var(--ink); }
</style>
</head>
<body>

  <section class="card card--front">
    <svg class="swoosh" viewBox="0 0 556 316" aria-hidden="true">
      <path d="M0,262 C150,300 320,250 556,12 L556,316 L0,316 Z" fill="var(--red)"/>
      <path d="M0,238 C120,280 280,250 392,176 C300,235 150,262 0,256 Z" fill="var(--green)"/>
    </svg>
    <div class="company-name">Brisk Property Developments</div>
    <div class="holder">
      <p class="holder__name">Lionel Brisk</p>
      <p class="holder__role">Manager/Director</p>
    </div>
    <div class="address">
      <p>Po Box 5347</p>
      <p>Marrowvale Central , Mvl</p>
    </div>
    <div class="contact">
      <p class="contact__line">
        <svg class="contact__icon" viewBox="0 0 12 12" aria-hidden="true"><circle cx="6" cy="6" r="5.2" fill="none" stroke="var(--white)" stroke-width="1.2"/><path d="M4,3.5 L5,3.5 L5.5,5 L4.8,5.6 C5.2,6.5 5.6,6.9 6.4,7.3 L7,6.6 L8.5,7.1 L8.5,8.1 C6,8.4 3.6,6 4,3.5 Z" fill="var(--white)"/></svg>
        0491 638 205
      </p>
      <p class="contact__line">
        <svg class="contact__icon" viewBox="0 0 12 12" aria-hidden="true"><rect x="1" y="3" width="10" height="7" fill="var(--white)"/><path d="M1,3 L6,7 L11,3" fill="none" stroke="var(--red)" stroke-width="1"/></svg>
        lionel@briskpropertydevelopments.com
      </p>
    </div>
  </section>

  <section class="card card--red">
    <div class="company-name">Brisk Property Developments</div>
    <p class="website">www.briskpropertydevelopments.com</p>
  </section>

  <section class="card card--white">
    <div class="company-name">Brisk Property Developments</div>
    <p class="website">www.briskpropertydevelopments.com</p>
  </section>

  <section class="card card--green">
    <div class="company-name">Brisk Property Developments</div>
    <p class="website">www.briskpropertydevelopments.com</p>
  </section>

</body>
</html>
```